Keystone Trench Co Business Card*

Looking for a professional, clean and crisp business card

I am in the underground utilities industry and am just looking for a really impressive business card. I would like our card to be white with our symbol crisp and clear with it protruding. I also have a business partner that will require his name and info on the card once the design is set. I would like to have our website info on the card which is;
http://keystonetrenchco.example/

Contact Information for Business Card

Website, contact name, number and email

```html
<!DOCTYPE html>
<html lang="en">
<head>
<meta charset="utf-8">
<title>Keystone Trench Co Business Card</title>
<link href="https://fonts.googleapis.com/css2?family=Roboto:wght@400;500&display=swap" rel="stylesheet">
<style>
  :root {
    --backdrop: #e9e9e9;
    --card: #ffffff;
    --card-edge: #3d63c9;
    --accent: #3d63c9;
    --icon: #3d63c9;
    --text-main: #2e2e30;
    --text-muted: #7a7a7a;
    --rule: #c4c4c4;
    --mark-back: #b9b9bc;
  }
  html, body {
    margin: 0;
    width: 1200px;
    height: 801px;
    overflow: hidden;
    background: var(--backdrop);
    font-family: "Roboto", Arial, sans-serif;
  }
  .stage {
    position: relative;
    width: 1200px;
    height: 801px;
  }
  .card {
    position: absolute;
    top: 246px;
    width: 525px;
    height: 300px;
    background: var(--card);
    border-left: 3px solid var(--card-edge);
    border-bottom: 3px solid var(--card-edge);
    box-sizing: border-box;
    overflow: hidden;
    box-shadow: 0 6px 18px rgba(0, 0, 0, 0.12);
  }
  .card-front { left: 50px; }
  .card-back { left: 625px; }

  .corner-tab {
    position: absolute;
    top: 0;
    right: 0;
    width: 14px;
    height: 22px;
    background: var(--accent);
  }
  .brand {
    position: absolute;
    display: flex;
    align-items: center;
    gap: 10px;
    font-weight: 500;
    white-space: nowrap;
  }
  .brand-dot {
    border-radius: 50%;
    flex: none;
  }
  .card-front .brand {
    left: 34px;
    top: 132px;
    color: var(--text-main);
    font-size: 17px;
  }
  .card-front .brand-dot {
    width: 18px;
    height: 18px;
    background: var(--text-main);
  }
  .card-back .brand {
    left: 50%;
    top: 50%;
    transform: translate(-50%, -50%);
    color: var(--mark-back);
    font-size: 26px;
  }
  .card-back .brand-dot {
    width: 26px;
    height: 26px;
    background: var(--mark-back);
  }

  .person {
    position: absolute;
    right: 34px;
    top: 34px;
    text-align: right;
  }
  .person-name {
    margin: 0;
    color: var(--accent);
    font-size: 22px;
    font-weight: 500;
    letter-spacing: 0.2px;
  }
  .person-role {
    margin: 2px 0 0;
    color: var(--text-muted);
    font-size: 13px;
  }
  .rule {
    position: absolute;
    height: 1px;
    background: var(--rule);
  }
  .rule-name { left: 255px; right: 30px; top: 100px; }
  .rule-contact { left: 230px; right: 30px; top: 200px; }

  .contact-list {
    position: absolute;
    left: 236px;
    top: 214px;
    margin: 0;
    padding: 0;
    list-style: none;
  }
  .contact-list li {
    display: flex;
    align-items: center;
    gap: 10px;
    height: 23px;
    color: var(--text-main);
    font-size: 14px;
  }
  .contact-list svg {
    width: 12px;
    height: 12px;
    flex: none;
  }
</style>
</head>
<body>
<main class="stage">

  <section class="card card-front" aria-label="Business card front">
    <span class="corner-tab"></span>

    <div class="brand">
      <span class="brand-dot"></span>
      <span class="brand-name">Keystone Trench Co</span>
    </div>

    <div class="person">
      <p class="person-name">Darren Kolwitz</p>
      <p class="person-role">Owner</p>
    </div>
    <span class="rule rule-name"></span>
    <span class="rule rule-contact"></span>

    <ul class="contact-list">
      <li>
        <svg viewBox="0 0 12 12" aria-hidden="true"><path d="M2.5 1 L4.5 1 L5.3 3.6 L4 4.6 C4.6 6 5.9 7.3 7.4 8 L8.4 6.7 L11 7.5 L11 9.5 C11 10.3 10.3 11 9.5 11 C5 11 1 7 1 2.5 C1 1.7 1.7 1 2.5 1 Z" fill="var(--icon)"/></svg>
        <span>604-555-0183(DIGS)</span>
      </li>
      <li>
        <svg viewBox="0 0 12 12" aria-hidden="true"><rect x="1" y="2.5" width="10" height="7" fill="none" stroke="var(--icon)" stroke-width="1.2"/><path d="M1 2.5 L6 6.5 L11 2.5" fill="none" stroke="var(--icon)" stroke-width="1.2"/></svg>
        <span>Darren@keystonetrenchco.example</span>
      </li>
      <li>
        <svg viewBox="0 0 12 12" aria-hidden="true"><circle cx="6" cy="6" r="5" fill="none" stroke="var(--icon)" stroke-width="1.2"/><path d="M1 6 H11 M6 1 C3.5 3.5 3.5 8.5 6 11 M6 1 C8.5 3.5 8.5 8.5 6 11" fill="none" stroke="var(--icon)" stroke-width="1"/></svg>
        <span>www.keystonetrenchco.example</span>
      </li>
    </ul>
  </section>

  <section class="card card-back" aria-label="Business card back">
    <div class="brand">
      <span class="brand-dot"></span>
      <span class="brand-name">Keystone Trench Co</span>
    </div>
  </section>

</main>
</body>
</html>
```